Brookmere Osteopathy flyer

I want a clean clear DL flyer (but also want an A4 poster) promoting a new Osteopathic business in a semi rural area in Tasmania (Australia).
It can have pictures like the examples attached to show people what Osteopathy is (its like Chiropractic and physiotherapy).
I am the sole practioner and am male, so any pictures would be best to be a white male if possible.
I've attached some wording, you can use all, or none of it
I don't have a phone number for the business yet
info@brookmereosteopathy.example
www.brookmereosteopathy.example
Target Market(s)
Australians, from tradies, professionals, babies to retired people
Industry/Entity Type
Health
Look and feel

```html
<!DOCTYPE html>
<html lang="en">
<head>
<meta charset="utf-8">
<title>Brookmere Osteopathy – DL Flyer</title>
<link href="https://fonts.googleapis.com/css2?family=Questrial&display=swap" rel="stylesheet">
<style>
  :root {
    --stage: #8a8a8e;
    --brand-blue: #0f97d2;
    --sky-blue: #1aa6e0;
    --deep-blue: #0b7fc0;
    --white: #ffffff;
    --ink: #3a3a3a;
    --sun-orange: #f7a21b;
    --photo-skin: #c99a78;
    --photo-light: #d8d4d0;
  }
  * { box-sizing: border-box; margin: 0; padding: 0; }
  html, body { width: 1200px; height: 1068px; overflow: hidden; }
  body {
    background: var(--stage);
    font-family: "Questrial", sans-serif;
    position: relative;
  }
  .flyer {
    position: absolute;
    top: 147px;
    width: 378px;
    height: 755px;
    overflow: hidden;
  }
  .flyer--front { left: 161px; background: var(--brand-blue); }
  .flyer--back { left: 661px; background: var(--white); }

  /* Front */
  .front-photo {
    position: absolute; left: 0; top: 0; width: 378px; height: 470px;
    background: linear-gradient(160deg, var(--photo-light) 0%, var(--photo-skin) 55%, #a8775a 100%);
  }
  .front-wave { position: absolute; left: 0; top: 400px; width: 378px; height: 120px; }
  .brand-mark {
    position: absolute; left: 98px; top: 481px; width: 182px; height: 182px;
    border: 3px solid var(--white); border-radius: 50%;
    display: flex; align-items: center; justify-content: center; text-align: center;
    color: var(--white); font-size: 22px; line-height: 1.2;
  }
  .front-phone {
    position: absolute; left: 0; width: 100%; top: 680px; text-align: center;
    color: var(--white); font-size: 31px; letter-spacing: 0.3px; white-space: nowrap;
  }
  .front-web {
    position: absolute; left: 0; width: 100%; top: 724px; text-align: center;
    color: var(--white); font-size: 12px; letter-spacing: 0.6px; white-space: nowrap;
  }

  /* Back */
  .back-photo {
    position: absolute; left: 0; top: 0; width: 378px; height: 520px;
    background: linear-gradient(170deg, var(--sky-blue) 0%, #2ab0e6 50%, var(--deep-blue) 100%);
  }
  .reasons { position: absolute; left: 53px; top: 38px; color: var(--white); }
  .reasons h2 {
    font-weight: 400; font-size: 20px; line-height: 20px; letter-spacing: 0.2px;
    text-transform: uppercase;
  }
  .reasons ul { list-style: none; margin-top: 10px; margin-left: 6px; }
  .reasons li { font-size: 13.5px; line-height: 21.8px; position: relative; padding-left: 18px; }
  .reasons li::before { content: "•"; position: absolute; left: 0; }
  .treatment-photo { position: absolute; border-radius: 50%; }
  .treatment-photo--infant {
    left: 25px; top: 320px; width: 154px; height: 154px;
    background: radial-gradient(circle at 50% 45%, #e9c8b4 0%, #b8c6d8 60%, #5aa0d2 100%);
  }
  .treatment-photo--adult {
    left: 201px; top: 316px; width: 152px; height: 152px;
    background: radial-gradient(circle at 55% 50%, #e0b9a0 0%, #d9dde4 55%, #b9c3cf 100%);
  }
  .back-wave { position: absolute; left: 0; top: 450px; width: 378px; height: 90px; }
  .about {
    position: absolute; left: 44px; top: 533px; width: 294px;
    color: var(--ink); font-size: 13px; line-height: 17.6px; text-align: justify;
    hyphens: manual;
  }
  .contact-mark {
    position: absolute; left: 37px; top: 625px; width: 96px; height: 96px;
    border: 2px solid var(--brand-blue); border-radius: 50%;
    display: flex; align-items: center; justify-content: center; text-align: center;
    color: var(--brand-blue); font-size: 12px; line-height: 1.25;
  }
  .contact { position: absolute; left: 144px; top: 633px; width: 200px; }
  .contact-phone {
    display: flex; align-items: center; gap: 5px;
    color: var(--brand-blue); font-size: 19px; white-space: nowrap;
  }
  .contact-phone svg { width: 21px; height: 21px; flex: none; }
  .contact-line { color: var(--ink); font-size: 11px; line-height: 17px; margin-left: 2px; white-space: nowrap; }
  .contact-line:first-of-type { margin-top: 3px; }
  .contact-web {
    position: absolute; left: 136px; top: 696px; width: 206px; height: 17px;
    background: var(--brand-blue); border-radius: 9px;
    color: var(--white); font-size: 8.5px; line-height: 17px; text-align: center; letter-spacing: 0.1px;
    white-space: nowrap;
  }
</style>
</head>
<body>

<section class="flyer flyer--front">
  <div class="front-photo" role="img" aria-label="Photo of a practitioner's hands massaging a patient's upper back and shoulder"></div>
  <svg class="front-wave" viewBox="0 0 378 120" preserveAspectRatio="none" aria-hidden="true">
    <path d="M0 85 C60 40 120 20 190 38 C260 56 320 40 378 20 L378 120 L0 120 Z" fill="var(--brand-blue)"/>
    <path d="M0 85 C60 40 120 20 190 38 C260 56 320 40 378 20" fill="none" stroke="var(--white)" stroke-width="10"/>
  </svg>
  <div class="brand-mark">Brookmere<br>Osteopathy</div>
  <div class="front-phone">Phone coming soon</div>
  <div class="front-web">WWW.BROOKMEREOSTEOPATHY.EXAMPLE</div>
</section>

<section class="flyer flyer--back">
  <div class="back-photo" role="img" aria-label="Blue-tinted photo of a practitioner treating a relaxed patient lying down"></div>
  <div class="reasons">
    <h2>Common reasons people<br>visit an osteopath:</h2>
    <ul>
      <li>Back / neck pain</li>
      <li>Headaches / migraines</li>
      <li>Joint and muscle pain</li>
      <li>Pregnancy-related discomfort</li>
      <li>Disc related issues</li>
      <li>Sciatica</li>
      <li>Plantar fasciitis</li>
      <li>Tendonitis / Bursitis</li>
      <li>Adhesive capsulitis (frozen shoulder)</li>
      <li>Tennis / Golfers elbow</li>
    </ul>
  </div>
  <div class="treatment-photo treatment-photo--infant" role="img" aria-label="Round photo of gentle osteopathic treatment for a sleeping baby"></div>
  <div class="treatment-photo treatment-photo--adult" role="img" aria-label="Round photo of a woman receiving head and neck treatment"></div>
  <svg class="back-wave" viewBox="0 0 378 90" preserveAspectRatio="none" aria-hidden="true">
    <path d="M0 72 C50 60 90 30 150 36 C220 44 260 70 310 52 C340 40 360 28 378 22 L378 90 L0 90 Z" fill="var(--white)"/>
    <path d="M0 72 C50 60 90 30 150 36 C220 44 260 70 310 52 C340 40 360 28 378 22" fill="none" stroke="var(--sky-blue)" stroke-width="8"/>
  </svg>
  <p class="about">Osteopaths use a combination of joint manip&shy;ulation, targeted deep tissue massage and stretching to improve function, relieve pain and support the body’s ability to heal itself.</p>
  <div class="contact-mark">Brookmere<br>Osteopathy</div>
  <div class="contact">
    <div class="contact-phone">
      <svg viewBox="0 0 24 24" aria-hidden="true">
        <circle cx="12" cy="12" r="12" fill="var(--sun-orange)"/>
        <path d="M8.2 6.5l1.8-.4 1.2 3-1.3 1c.6 1.4 1.6 2.5 3 3.2l1-1.3 3 1.1-.3 1.9c-.2.8-.9 1.3-1.7 1.2C10.6 15.7 7.6 12.6 7.1 8.3c-.1-.8.4-1.6 1.1-1.8z" fill="var(--white)"/>
      </svg>
      <span>Phone coming soon</span>
    </div>
    <div class="contact-line">info@brookmereosteopathy.example</div>
    <div class="contact-line">24 Millbrook Lane, Brookmere</div>
  </div>
  <div class="contact-web">WWW.BROOKMEREOSTEOPATHY.EXAMPLE</div>
</section>

</body>
</html>
```